CREATE A BUSINESS CARD FOR A BOAT CLEANING SERVICE

WE ARE STARTING A NEW BOAT CLEANING BUSINESS. WE DIVE UNDERWATER TO CLEAN BOAT HULLS, JETTIES, UNDERWATER STRUCTURES ETC. WE ARE LOOKING FOR AN UPPERMARKET MODERN LOGO AND BUSINESS CARD AS ALOT OF OUR TARGET MARKET WILL BE HIGH END. YOU HAVE TO DESIGN A BUSINESS CARD AND LOGO SEPERATELY .
THE BUSINESS CARD DIMESNION MUST BE STANDARD SIZE.
The standard dimensions of a printed business card are 3.5 x 2 inches

Target Market(s)

UNDERWATER SERVICED

Industry/Entity Type

Business

Contact Information for Business Card

HOLLAND UNDERWATER SERVICES

Font styles to use
Serif

Colors

Designer to choose colors to be used in the design.

Requirements
Must have
• HOLLAND
Nice to have
• dark
Should not have
• more than 3 colors

```html
<!DOCTYPE html>
<html lang="en">
<head>
<meta charset="utf-8">
<title>Holland Underwater Services – Business Card</title>
<link href="https://fonts.googleapis.com/css2?family=Open+Sans:wght@300;400;600&display=swap" rel="stylesheet">
<style>
  :root {
    --page-bg: #e9e7e3;
    --card-white: #ffffff;
    --card-shade: #eef0f2;
    --brand-blue: #1f73b7;
    --brand-light: #4a9cc8;
    --band-deep: #175e9c;
    --stripe-grey: #b9bdc2;
    --text-grey: #a4a8ad;
  }
  html, body {
    margin: 0;
    width: 1200px;
    height: 1023px;
    overflow: hidden;
    background: var(--page-bg);
  }
  .canvas {
    position: relative;
    width: 1200px;
    height: 1023px;
  }
  .business-card {
    position: absolute;
    left: 75px;
    top: 211px;
    width: 1050px;
    height: 600px;
    filter: drop-shadow(0 14px 26px rgba(0,0,0,0.18));
  }
  .card-text { font-family: "Open Sans", sans-serif; }
  .brand-name { font-weight: 400; fill: var(--brand-light); }
  .person-name { font-weight: 600; fill: var(--brand-light); letter-spacing: 1px; }
  .person-role { font-weight: 300; fill: var(--text-grey); }
  .contact-line { font-weight: 300; fill: var(--text-grey); }
  .footer-name { font-weight: 300; fill: var(--text-grey); }
</style>
</head>
<body>
<div class="canvas">
  <svg class="business-card" viewBox="0 0 1050 600" xmlns="http://www.w3.org/2000/svg">
    <defs>
      <linearGradient id="cardFace" x1="0" y1="0" x2="1" y2="1">
        <stop offset="0" stop-color="var(--card-shade)"/>
        <stop offset="0.45" stop-color="var(--card-white)"/>
        <stop offset="1" stop-color="var(--card-shade)"/>
      </linearGradient>
      <linearGradient id="bandBlue" x1="0" y1="0" x2="1" y2="0">
        <stop offset="0" stop-color="var(--brand-light)"/>
        <stop offset="0.35" stop-color="var(--brand-blue)"/>
        <stop offset="1" stop-color="var(--band-deep)"/>
      </linearGradient>
      <clipPath id="cardShape"><rect width="1050" height="600" rx="26"/></clipPath>
    </defs>

    <g clip-path="url(#cardShape)">
      <rect class="card-face" width="1050" height="600" fill="url(#cardFace)"/>
      <path class="band-stripe" d="M0,462 C320,480 700,530 1050,532 L1050,600 L0,600 Z" fill="var(--stripe-grey)"/>
      <path class="band-blue" d="M0,478 C320,496 700,546 1050,548 L1050,600 L0,600 Z" fill="url(#bandBlue)"/>
    </g>

    <!-- brand block: plain square with company name -->
    <rect class="brand-square" x="235" y="150" width="60" height="60" fill="var(--brand-light)"/>
    <text class="card-text brand-name" x="265" y="262" font-size="22" text-anchor="middle">Holland Underwater Services</text>

    <line class="divider" x1="470" y1="110" x2="470" y2="330" stroke="var(--brand-light)" stroke-width="1.5"/>

    <!-- contact block -->
    <text class="card-text person-name" x="510" y="132" font-size="30">MARTIN KEANE</text>
    <text class="card-text person-role" x="512" y="160" font-size="17">President</text>
    <text class="card-text contact-line" x="512" y="198" font-size="18">410, 318- 6th Street, NW</text>
    <text class="card-text contact-line" x="512" y="224" font-size="18">Harbourview, BC V4K 2M9</text>

    <g class="contact-icons" fill="none" stroke="var(--brand-blue)" stroke-width="1.6">
      <path d="M514,252 q2,-3 5,0 l2,3 q1,2 -1,3 q2,4 5,6 q1,-2 3,-1 l3,2 q3,2 0,5 q-3,3 -8,0 q-6,-4 -9,-11 q-1,-5 0,-7 z"/>
      <rect x="513" y="280" width="14" height="10" rx="1"/>
      <path d="M513,281 l7,5 l7,-5"/>
      <circle cx="520" cy="312" r="7"/>
      <path d="M513,312 h14 M520,305 q-4,7 0,14 q4,-7 0,-14"/>
    </g>
    <text class="card-text contact-line" x="538" y="264" font-size="18">(555) 218-4630</text>
    <text class="card-text contact-line" x="538" y="292" font-size="18">info@hollandunderwater.com</text>
    <text class="card-text contact-line" x="538" y="320" font-size="18">www.hollandunderwater.com</text>

    <!-- partner badge and footer name -->
    <circle class="partner-badge" cx="536" cy="400" r="22" fill="var(--brand-light)"/>
    <text class="card-text footer-name" x="574" y="406" font-size="17">Holland Underwater Services</text>
  </svg>
</div>
</body>
</html>
```